Business Card for Field Lotus-Eco Friendly Organic Clothing Brand

We are looking for an amazing business card for our eco friendly, organic clothing brand. We are thinking maybe a business card with a peel off sticker on the back, since our hanging clothing tag is a peel off sticker on the back. I will attach our hang tag so we can make sure we stay in line with our design. I've also attached a bag we are doing because I do like the scattered emblem look as well.

```html
<!DOCTYPE html>
<html lang="en">
<head>
<meta charset="utf-8">
<title>Field Lotus – Business Card</title>
<link rel="stylesheet" href="https://fonts.googleapis.com/css2?family=Open+Sans:wght@400;600;700&display=swap">
<style>
  :root {
    --backdrop: #3a3230;
    --card-black: #0c0c0c;
    --card-charcoal: #262624;
    --gold: #e2b523;
    --gold-light: #f6d76a;
    --gold-deep: #a8791a;
    --ink-light: #eeeeee;
  }
  html, body {
    margin: 0;
    width: 1200px;
    height: 900px;
    overflow: hidden;
    background: var(--backdrop);
    font-family: "Open Sans", Arial, sans-serif;
  }
  .sheet {
    position: relative;
    width: 1200px;
    height: 900px;
    display: flex;
    align-items: center;
    justify-content: center;
    gap: 40px;
  }
  .card {
    position: relative;
    width: 540px;
    height: 310px;
    box-shadow: 0 10px 30px rgba(0,0,0,.45);
    overflow: hidden;
  }

  /* Front face */
  .card-front { background: var(--card-black); }
  .brand-block {
    position: absolute;
    left: 30px;
    top: 120px;
    display: flex;
    align-items: center;
    gap: 12px;
  }
  .brand-mark {
    width: 28px;
    height: 28px;
    background: var(--gold);
    flex: none;
  }
  .brand-name {
    font-weight: 700;
    font-size: 28px;
    color: var(--gold);
    line-height: 1;
    white-space: nowrap;
  }
  .brand-url {
    position: absolute;
    left: 70px;
    top: 160px;
    font-size: 9px;
    color: var(--ink-light);
  }
  .divider {
    position: absolute;
    left: 258px;
    top: 70px;
    width: 1px;
    height: 170px;
    background: linear-gradient(to bottom, transparent, var(--gold), transparent);
  }
  .contact {
    position: absolute;
    left: 282px;
    top: 76px;
    color: var(--ink-light);
    font-size: 13px;
    line-height: 1.35;
    white-space: nowrap;
  }
  .contact-name {
    margin: 0;
    color: var(--gold);
    font-weight: 700;
    font-size: 15px;
  }
  .contact-role { margin: 0 0 14px; }
  .contact-address { margin: 0 0 14px; }
  .contact-list { list-style: none; margin: 0; padding: 0; }
  .contact-list li { display: flex; align-items: center; gap: 10px; }
  .contact-list svg { width: 10px; height: 10px; fill: var(--gold); flex: none; }

  /* Back face */
  .card-back { background: var(--card-charcoal); }
  .motif-field {
    position: absolute;
    inset: 0;
    background:
      radial-gradient(circle at 30% 30%, rgba(226,181,35,.35), transparent 55%),
      radial-gradient(circle at 75% 20%, rgba(246,215,106,.3), transparent 50%),
      linear-gradient(135deg, #2e2b22, #3c3425 50%, #262624);
  }
  .name-plate {
    position: absolute;
    left: 130px;
    right: 18px;
    top: 168px;
    height: 78px;
    border: 3px solid var(--gold);
    background: rgba(20,20,18,.55);
    display: flex;
    align-items: center;
    justify-content: center;
  }
  .name-plate span {
    font-weight: 700;
    font-size: 44px;
    color: var(--gold);
  }
</style>
</head>
<body>
<main class="sheet">
  <section class="card card-front" aria-label="Business card front">
    <div class="brand-block">
      <span class="brand-mark"></span>
      <span class="brand-name">Field Lotus</span>
    </div>
    <span class="brand-url">www.fieldlotus.com</span>
    <div class="divider"></div>
    <div class="contact">
      <p class="contact-name">Daniel Marsh</p>
      <p class="contact-role">Managing Director</p>
      <p class="contact-address">48 Cedar Lane, Suite Seven<br>Harbor Vale, 908172.</p>
      <ul class="contact-list">
        <li><svg viewBox="0 0 10 10"><path d="M2 0.5 L3.8 2.6 L2.8 3.8 Q4 6 6.2 7.2 L7.4 6.2 L9.5 8 L8 9.5 Q3 9 0.5 2 Z"/></svg>055-318 204 667</li>
        <li><svg viewBox="0 0 10 10"><path d="M0 2 H10 V8 H0 Z M0 2 L5 5.5 L10 2" stroke="#0c0c0c" stroke-width=".8"/></svg>info@fieldlotus-mail.com</li>
        <li><svg viewBox="0 0 10 10"><circle cx="5" cy="5" r="5"/></svg>www.fieldlotus-shop.com</li>
      </ul>
    </div>
  </section>

  <section class="card card-back" aria-label="Business card back">
    <div class="motif-field" role="img" aria-label="Scattered gold foil words and peace, heart and om emblems"></div>
    <div class="name-plate"><span>Field Lotus</span></div>
  </section>
</main>
</body>
</html>
```